Venture 482 - Lumora Book Cover

I am looking for a Lumora book cover for my book about "Venture 482".
The Book is Titled:
Venture 482 Ascended
Shaping Outcomes: Paths To Unlocking Cosmic Truths
Author is Dorian Pell
Here is a book description that may help you understand more about it:
Inspired by the genius of Edwin Marlowe, this comprehensive guide delves into the ancient wisdom and cutting-edge science behind the 482 method, a powerful tool for manifesting your desires. Whether you're seeking personal growth, financial success, or spiritual enlightenment, this book provides advanced techniques and methods to transform your dreams into reality.
Any questions please ask.
Thanks
Owen

```html
<!DOCTYPE html>
<html lang="en">
<head>
<meta charset="utf-8">
<title>Venture 482 Ascended — Dorian Pell</title>
<link rel="stylesheet" href="https://fonts.googleapis.com/css2?family=Cinzel:wght@400;500&family=Tinos&display=swap">
<style>
  :root {
    --page-bg: #d9d9d9;
    --cover-top: #101a22;
    --cover-mid: #1e2c36;
    --cover-bottom: #141d25;
    --ember: #e0643a;
    --ember-deep: #a9391c;
    --cream: #fbeadb;
    --cream-soft: #f6e3d2;
  }
  * { margin: 0; padding: 0; box-sizing: border-box; }
  html, body {
    width: 1200px;
    height: 1131px;
    overflow: hidden;
    background: var(--page-bg);
  }
  .cover {
    position: absolute;
    left: 250px;
    top: 38px;
    width: 700px;
    height: 1054px;
    overflow: hidden;
    background: linear-gradient(180deg, var(--cover-top) 0%, var(--cover-mid) 30%, var(--cover-mid) 80%, var(--cover-bottom) 100%);
    color: var(--cream);
    text-align: center;
  }
  .cover-art {
    position: absolute;
    left: 50px;
    top: 0;
    width: 600px;
    height: 1054px;
    background:
      linear-gradient(90deg, transparent 44%, rgba(224,100,58,0.55) 48%, rgba(224,100,58,0.55) 52%, transparent 56%) top / 100% 30% no-repeat,
      radial-gradient(ellipse 48% 26% at 50% 30%, rgba(224,100,58,0.6) 0%, rgba(169,57,28,0.35) 50%, transparent 100%),
      radial-gradient(ellipse 10% 45% at 50% 62%, rgba(224,100,58,0.45) 0%, transparent 100%);
  }
  .author {
    position: absolute;
    top: 62px;
    left: 0;
    width: 100%;
    font-family: "Cinzel", serif;
    font-weight: 400;
    font-size: 47px;
    letter-spacing: 0.22em;
    color: var(--cream-soft);
  }
  .title {
    position: absolute;
    left: 0;
    width: 100%;
    font-family: "Cinzel", serif;
    font-weight: 400;
    color: var(--cream);
    text-shadow: 0 4px 10px rgba(0,0,0,0.55);
  }
  .title-word { top: 470px; font-size: 118px; line-height: 1; letter-spacing: -0.01em; }
  .title-number { top: 575px; font-size: 300px; line-height: 1; letter-spacing: -0.04em; }
  .title-edition { top: 828px; font-size: 58px; line-height: 1; letter-spacing: 0.38em; padding-left: 0.38em; }
  .subtitle-lead {
    position: absolute;
    top: 907px;
    left: 0;
    width: 100%;
    font-family: "Tinos", serif;
    font-size: 27px;
    color: var(--cream);
  }
  .subtitle {
    position: absolute;
    top: 950px;
    left: 0;
    width: 100%;
    font-family: "Tinos", serif;
    font-size: 25px;
    line-height: 34px;
    color: var(--cream);
  }
</style>
</head>
<body>
  <main class="cover">
    <div class="cover-art" role="img" aria-label="Silhouette of a standing figure radiating an orange geometric energy web against a dark navy field"></div>
    <p class="author">DORIAN PELL</p>
    <h1>
      <span class="title title-word">Venture</span>
      <span class="title title-number">482</span>
      <span class="title title-edition">ASCENDED</span>
    </h1>
    <p class="subtitle-lead">SHAPING OUTCOMES:</p>
    <p class="subtitle">Paths to unlocking<br>cosmic truths</p>
  </main>
</body>
</html>
```